Brand new letterhead, business card, email signature etc.

We are a financial company in London, UK. Our website is www.marlowvane.com. We're wanting a complete remodel of the company colours, letter head, business cards, email signatures, etc. Looking to keep the same font for the company name. I have upload a colour palette that we want to work with. We're looking for company letterhead for outgoing letters/ correspondence, letterhead for internal documentation, email signatures, e-letters. etc. Ultimately we will redesign the entire website also. It is important that our clients get a strong, secure, warm, trustworthy, solid feeling and first impression.
Updates

Designs look the same

Target Market(s)

Institutional investors, (ultra) high net worth individuals

Industry/Entity Type

Finance, Invesments banking.

Font styles to use
Other font styles liked:
• Current font is "Champagne & Limousines"

Requirements
Must have
• Must use the colours provided on the PDF uploaded to the portal. The purple = main colour. The red = accent colour.
Nice to have
• Nice to use same font as now for the company name "Corvane". Font is "Champagne & Limousines". Nice to have some reference to the old logo flower, but only subtle.
Should not have
• Do not use the colour red from our website. Use the colours provided on the colour palette PDF that I uploaded in the portal.

```html
<!DOCTYPE html>
<html lang="en">
<head>
<meta charset="utf-8">
<title>Corvane Letterhead</title>
<link rel="stylesheet" href="https://fonts.googleapis.com/css2?family=Lato:wght@400;700&family=Kaushan+Script&display=swap">
<style>
  :root {
    --canvas: #e9e9ea;
    --paper: #ffffff;
    --ink: #231f20;
    --plum: #2c0e1c;
    --accent-red: #c21a37;
    --muted: #4a4446;
  }
  * { box-sizing: border-box; margin: 0; padding: 0; }
  html, body {
    width: 1200px; height: 874px; overflow: hidden;
    background: var(--canvas);
  }
  .letterhead {
    position: absolute; left: 320px; top: 41px;
    width: 560px; height: 792px;
    background: var(--paper);
    box-shadow: 0 4px 18px rgba(0,0,0,0.12);
    font-family: "Lato", sans-serif;
    color: var(--ink);
    overflow: hidden;
  }
  .brand {
    position: absolute; left: 44px; top: 82px;
    display: flex; align-items: center; gap: 10px;
  }
  .brand-dot {
    width: 10px; height: 10px; border-radius: 50%;
    background: var(--plum);
  }
  .brand-name {
    font-family: "Lato", sans-serif; font-weight: 400;
    font-size: 28px; letter-spacing: 1px; color: var(--plum);
    line-height: 1;
  }
  .contact {
    position: absolute; right: 40px; top: 30px;
    display: flex; gap: 12px; align-items: stretch;
    font-size: 6.6px; color: var(--muted); line-height: 1.45;
  }
  .contact-rule { width: 1px; background: var(--ink); }
  .contact-list { list-style: none; padding-top: 2px; }
  .contact-list li { display: flex; align-items: center; gap: 4px; }
  .contact-list svg { width: 6px; height: 6px; fill: var(--ink); }
  .contact-address { margin-top: 4px; }
  .letter {
    position: absolute; left: 44px; top: 160px; width: 460px;
    font-size: 10px; line-height: 1.42;
  }
  .letter-date { margin-bottom: 12px; }
  .recipient { margin-left: 20px; margin-bottom: 10px; }
  .recipient-org { margin-top: 8px; }
  .salutation { font-weight: 700; font-size: 13px; margin: 0 0 10px 20px; }
  .body-copy { margin-left: 20px; }
  .body-copy p { margin-bottom: 14px; }
  .closing { margin: 14px 0 0 90px; }
  .signature {
    font-family: "Kaushan Script", cursive; font-size: 26px;
    margin: 26px 0 0 110px; color: var(--ink);
  }
  .footer-swoosh {
    position: absolute; left: 0; bottom: 0; width: 560px; height: 230px;
  }
</style>
</head>
<body>
  <main class="letterhead">
    <header>
      <div class="brand">
        <span class="brand-dot"></span>
        <span class="brand-name">Corvane</span>
      </div>
      <div class="contact">
        <span class="contact-rule"></span>
        <div>
          <ul class="contact-list">
            <li><svg viewBox="0 0 10 10"><circle cx="5" cy="5" r="5"/></svg>020 7946 0321</li>
            <li><svg viewBox="0 0 10 10"><rect x="0" y="2" width="10" height="6"/></svg>info@marlowvane.com</li>
            <li><svg viewBox="0 0 10 10"><circle cx="5" cy="5" r="5"/></svg>www.marlowvane.com</li>
          </ul>
          <p class="contact-address">Corvane Group Limited<br>4th Floor 18 Halden Row<br>London EC2M 7QL</p>
        </div>
      </div>
    </header>

    <section class="letter">
      <p class="letter-date">January-03-2020</p>
      <div class="recipient">
        <p>Mr. Adam Reyes<br>President</p>
        <p class="recipient-org">Northgate Holdings<br>123 Street Name, Suite# 10<br>City, State, 120023</p>
      </div>
      <p class="salutation">Dear Mr. Adam</p>
      <div class="body-copy">
        <p>Lorem ipsum dolor sit amet, consectetur adipiscing elit, sed do eiusmod tempor incididunt ut labore et dolore magna aliqua. Ut enim ad minim veniam, quis nostrud exercitation ullamco laboris nisi ut aliquip ex ea commodo consequat. Duis aute irure dolor in reprehenderit in voluptate velit esse cillum dolore eu fugiat nulla pariatur.</p>
        <p>Lorem ipsum dolor sit amet, consectetur adipiscing elit, sed do eiusmod tempor incididunt ut labore et dolore magna aliqua. Ut enim ad minim veniam, quis nostrud exercitation ullamco laboris nisi ut aliquip ex ea commodo consequat. Duis aute irure dolor in reprehenderit in voluptate velit esse cillum dolore eu fugiat nulla pariatur.</p>
        <p>Lorem ipsum dolor sit amet, consectetur adipiscing elit, sed do eiusmod tempor incididunt ut labore et dolore magna aliqua. Ut enim ad minim veniam, quis nostrud exercitation ullamco laboris nisi ut aliquip ex ea commodo consequat.</p>
        <p>Excepteur sint occaecat cupidatat non proident, sunt in culpa qui officia deserunt mollit anim id est laborum, re et dolore magnam aliquam quaerat voluptatem.</p>
      </div>
      <p class="closing">Regards</p>
      <p class="signature">Elena Hart</p>
    </section>

    <svg class="footer-swoosh" viewBox="0 0 560 230" preserveAspectRatio="none" aria-hidden="true">
      <path d="M0,230 L0,226 C120,218 200,192 300,152 C400,112 480,92 560,86 L560,230 Z" fill="var(--plum)"/>
      <path d="M0,218 C120,210 200,184 300,144 C400,104 480,84 560,78" fill="none" stroke="var(--accent-red)" stroke-width="4"/>
    </svg>
  </main>
</body>
</html>
```